Flat Belly Design Graphics for Social

I want to create 9 social media graphics (new Instagram size 4:5 (1080 x 1350 pixels) focusing on our Flat Belly Graphics, using the pics attached. Use the attached pics, NO RANDOM STOCK PHOTOGRAPHY. For the color scheme of the graphics, the color palette is attached. YOU MUST POST ALL 9 GRAPHICS IN ONE ENTRY.
Using the 3 titles below, create one set of graphics. 1) with all text, then for the others, use the pictures as detailed below in IMPORTANT:
1. Ten-Week Bright Morning Reboot
2. The Quick Garden Kitchen Menu Guide
3. Studio Habits for Lasting Energy Past Midlife - Zero Gym Needed
IMPORTANT:
Only use RK Pic 1 and RK Pic 2 with the title, Ten-Week Bright Morning Reboot
Only use meal plan1 and meal plan2 pics with the title, Quick Garden Kitchen Menu Guide
Only use studio habits 1 and studio habits 2 pics with the title, Studio Habits for Lasting Energy Past Midlife - Zero Gym Needed
women over 40

```html
<!DOCTYPE html>
<html lang="en">
<head>
<meta charset="utf-8">
<title>Morning Reboot Social Set</title>
<link href="https://fonts.googleapis.com/css2?family=Bebas+Neue&display=swap" rel="stylesheet">
<style>
  :root{
    --backdrop:#200008;
    --blush:#f9ecec;
    --forest:#2f4f4b;
    --rose:#b5506e;
    --pink:#e396ab;
    --pink-soft:#e8a6b7;
    --pink-text:#f9e3ea;
    --white:#ffffff;
  }
  *{margin:0;padding:0;box-sizing:border-box}
  html,body{width:1075px;height:1200px;overflow:hidden;background:var(--backdrop)}
  body{position:relative;font-family:"Bebas Neue",Impact,sans-serif;line-height:.92}
  .post{position:absolute;width:217px;height:271px;overflow:hidden;background:var(--blush)}
  .col-1{left:197px}.col-2{left:428px}.col-3{left:662px}
  .row-1{top:177px}.row-2{top:464px}.row-3{top:755px}

  /* corner dot accents */
  .dots{position:absolute;width:26px;height:9px;background:var(--forest);opacity:.55}
  .dots.tl{top:8px;left:8px}.dots.tr{top:8px;right:8px}
  .dots.bl{bottom:8px;left:8px}.dots.br{bottom:8px;right:8px}

  /* typographic posts */
  .type-stack{position:absolute;inset:0;display:flex;flex-direction:column;align-items:center;justify-content:center;text-align:center}
  .type-stack span{display:block;white-space:nowrap}
  .green{color:var(--forest)}
  .rose{color:var(--rose)}

  /* circle posts */
  .band{position:absolute;background:var(--forest);color:var(--white);text-align:center;display:flex;flex-direction:column;justify-content:center;align-items:center;white-space:nowrap;padding-top:2px}
  .ring{position:absolute;width:166px;height:166px;border-radius:50%;border:2px solid var(--forest);left:25px;display:flex;align-items:center;justify-content:center}
  .ring .photo{width:152px;height:152px;border-radius:50%}
  .tagline{position:absolute;left:0;right:0;text-align:center;color:var(--pink);white-space:nowrap}

  .photo-warm{background:linear-gradient(160deg,#8c6b55,#e9dfd8 60%,#3a2e2a)}
  .photo-food{background:linear-gradient(135deg,#6b3f2a,#c84a3c 35%,#efece6 60%,#4d6b2e)}
  .photo-duo{background:linear-gradient(140deg,#3a2418,#c89a7c 50%,#f1ece8)}

  /* bold posts */
  .bold-forest{background:var(--forest)}
  .hero-photo{position:absolute;left:80px;top:0;width:137px;height:160px;background:linear-gradient(180deg,#3b524e,#d8c4b8 45%,#f4f0ec 70%,#2f4f4b)}
  .hero-title{position:absolute;right:14px;top:158px;text-align:right;color:var(--white);white-space:nowrap}
  .hero-title span{display:block}
  .hero-tag{position:absolute;right:14px;top:233px;width:124px;height:29px;background:var(--pink);color:var(--pink-text);font-size:26px;display:flex;align-items:center;justify-content:center;padding-top:2px}
  .center-strip{position:absolute;left:37px;top:0;width:144px;height:271px;background:var(--pink)}
  .strip-head{position:absolute;left:37px;width:144px;top:8px;text-align:center;color:var(--pink-text);font-size:22px;white-space:nowrap}
  .strip-head span{display:block}
  .strip-foot{position:absolute;left:37px;width:144px;bottom:7px;text-align:center;color:var(--forest);font-size:27px;white-space:nowrap}
  .arc-text{position:absolute;left:0;right:0;top:170px;text-align:center;color:var(--pink-text);font-size:22px;white-space:nowrap}
  .arc-text span{display:block}
  .base-bar{position:absolute;left:0;right:0;bottom:0;height:41px;background:var(--forest);color:var(--white);font-size:25px;display:flex;align-items:center;justify-content:center;padding-top:2px}
  svg{position:absolute;left:0;top:0}
</style>
</head>
<body>

<!-- Row 1: type only -->
<section class="post row-1 col-1">
  <i class="dots tl"></i><i class="dots tr"></i><i class="dots bl"></i><i class="dots br"></i>
  <div class="type-stack">
    <span class="green" style="font-size:42px">Ten-Week</span>
    <span class="rose" style="font-size:52px">Bright</span>
    <span class="rose" style="font-size:44px">Morning</span>
    <span class="green" style="font-size:34px">Reboot</span>
  </div>
</section>

<section class="post row-1 col-2">
  <i class="dots tl"></i><i class="dots tr"></i><i class="dots bl"></i><i class="dots br"></i>
  <div class="type-stack">
    <span class="green" style="font-size:27px">The Quick Garden</span>
    <span class="rose" style="font-size:52px">Kitchen</span>
    <span class="rose" style="font-size:62px">Menu</span>
    <span class="green" style="font-size:38px">Guide</span>
  </div>
</section>

<section class="post row-1 col-3">
  <i class="dots tl"></i><i class="dots tr"></i><i class="dots bl"></i><i class="dots br"></i>
  <div class="type-stack">
    <span class="green" style="font-size:32px">Studio Habits</span>
    <span class="green" style="font-size:33px">For Lasting</span>
    <span class="rose" style="font-size:33px">Energy Past</span>
    <span class="rose" style="font-size:50px">Midlife</span>
    <span class="green" style="font-size:22px">Zero Gym Needed</span>
  </div>
</section>

<!-- Row 2: circle frames -->
<section class="post row-2 col-1">
  <div class="band" style="left:13px;top:16px;width:194px;height:30px;font-size:20px">Ten-Week Bright Morning</div>
  <div class="ring" style="top:59px"><div class="photo photo-warm" role="img" aria-label="Smiling woman in a white cropped sweater showing her midsection"></div></div>
  <div class="tagline" style="top:234px;font-size:28px">Reboot</div>
</section>

<section class="post row-2 col-2">
  <div class="band" style="left:27px;top:6px;width:163px;height:58px;font-size:24px"><span>The Quick Garden</span><span>Kitchen</span></div>
  <div class="ring" style="top:69px"><div class="photo photo-food" role="img" aria-label="Healthy foods around a written meal plan sheet"></div></div>
  <div class="tagline" style="top:241px;font-size:28px">Menu Guide</div>
</section>

<section class="post row-2 col-3">
  <div class="band" style="left:7px;top:6px;width:203px;height:58px;font-size:21px"><span>Studio Habits For Lasting</span><span>Energy Past Midlife</span></div>
  <div class="ring" style="top:69px"><div class="photo photo-duo" role="img" aria-label="Two women sharing a secret, one looking surprised"></div></div>
  <div class="tagline" style="top:241px;font-size:27px">Zero Gym Needed</div>
</section>

<!-- Row 3: bold colour blocks -->
<section class="post row-3 col-1 bold-forest">
  <svg width="217" height="271" viewBox="0 0 217 271" aria-hidden="true">
    <path d="M0 0 H125 C95 40 70 45 52 80 C38 110 45 160 30 190 C20 208 10 215 0 220 Z" fill="var(--pink)"/>
    <path d="M125 0 C95 40 70 45 52 80 C38 110 45 160 30 190 C20 208 10 215 0 220" fill="none" stroke="var(--pink-text)" stroke-width="2"/>
  </svg>
  <div class="hero-photo" role="img" aria-label="Smiling woman in a white cropped sweater pointing to her waist"></div>
  <div class="hero-title"><span style="font-size:38px">Ten-Week</span><span style="font-size:32px">Bright Morning</span></div>
  <div class="hero-tag">Reboot</div>
</section>

<section class="post row-3 col-2 bold-forest">
  <div class="center-strip"></div>
  <div class="strip-head"><span>The Quick Garden</span><span>Kitchen</span></div>
  <svg width="217" height="271" viewBox="0 0 217 271" role="img" aria-label="Fresh salmon, vegetables and fruit around a meal plan notebook">
    <defs>
      <linearGradient id="foodTone" x1="0" y1="0" x2="1" y2="1">
        <stop offset="0" stop-color="#c8402f"/>
        <stop offset=".45" stop-color="#4a3528"/>
        <stop offset=".7" stop-color="#efeae2"/>
        <stop offset="1" stop-color="#e0783e"/>
      </linearGradient>
    </defs>
    <path d="M62 74 Q74 62 92 62 L126 62 Q144 62 156 74 L196 140 Q204 152 196 164 L156 222 Q146 234 128 234 L90 234 Q72 234 62 222 L22 164 Q14 152 22 140 Z" fill="url(#foodTone)" stroke="var(--white)" stroke-width="3"/>
  </svg>
  <div class="strip-foot">Menu Guide</div>
</section>

<section class="post row-3 col-3" style="background:var(--pink)">
  <svg width="217" height="271" viewBox="0 0 217 271" role="img" aria-label="Two women against a light blue wall, one whispering to the other">
    <defs>
      <linearGradient id="skyTone" x1="0" y1="0" x2="1" y2="1">
        <stop offset="0" stop-color="#6cc6da"/>
        <stop offset=".5" stop-color="#d9b49c"/>
        <stop offset="1" stop-color="#72c8dc"/>
      </linearGradient>
    </defs>
    <path d="M0 0 H217 V90 C195 150 95 180 0 112 Z" fill="url(#skyTone)"/>
    <path d="M217 90 C195 150 95 180 0 112" fill="none" stroke="var(--white)" stroke-width="2"/>
  </svg>
  <div class="arc-text"><span>Studio Habits For Lasting</span><span>Energy Past Midlife</span></div>
  <div class="base-bar">Zero Gym Needed</div>
</section>

</body>
</html>
```